Home Security Company Business Card

Looking for a eye catching business card that is non traditional and stands out but yet still looks professional. It should include all the pertinent information such as name, title, address, telephone, e-mail, website address should definitely stand out and then finally the logo.

Target Market(s)

Residential and Commercial accounts mostly upscale accounts

Industry/Entity Type

Security

Contact Information for Business Card

Name
Title
Address
Office #
Cell #
E-mail
Website

Font styles to use
Serif
Sans Serif

Requirements
Must have
• Logo, two sided color configuration
Nice to have
• You decide
Should not have
• There really aren't any.

```html
<!DOCTYPE html>
<html lang="en">
<head>
<meta charset="utf-8">
<title>Ironhaven Security Systems – Business Card</title>
<link href="https://fonts.googleapis.com/css2?family=Tinos:wght@400&family=Noto+Serif:wght@400&family=Open+Sans:wght@400&display=swap" rel="stylesheet">
<style>
  :root{
    --maroon:#7b1416;
    --gold:#e2b53e;
    --white:#ffffff;
    --stage:#efe6d6;
    --rule:#a8595a;
  }
  *{margin:0;padding:0;box-sizing:border-box}
  html,body{width:1189px;height:1200px;overflow:hidden}
  body{background:var(--stage);position:relative}

  .card{position:absolute;left:171px;width:856px;height:487px;border-radius:23px}
  .card--front{top:68px;background:var(--maroon)}
  .card--back{top:627px;background:var(--white)}

  .brand{position:absolute;display:block;overflow:visible}
  .brand text{font-family:'Tinos',serif;font-weight:400}

  .brand-dot{position:absolute;border-radius:50%}
  .card--front .brand-dot{left:103px;top:187px;width:114px;height:114px;background:var(--white)}
  .card--back .brand-dot{left:176px;top:146px;width:110px;height:110px;background:var(--gold)}

  .divider{position:absolute;left:423px;top:95px;width:1px;height:292px;background:var(--rule)}

  .contact{position:absolute;left:463px;top:100px;color:var(--maroon);font-family:'Noto Serif',serif}
  .contact__name{font-size:35px;line-height:36px;letter-spacing:.3px}
  .contact__title{font-family:'Open Sans',sans-serif;color:var(--gold);font-size:20px;line-height:22px;letter-spacing:.8px}
  .contact__address{margin-top:26px;font-size:22px;line-height:29px;letter-spacing:.3px}
  .contact__lines{list-style:none;margin-top:9px}
  .contact__lines li{display:flex;align-items:center;height:31px;font-size:21px;letter-spacing:.3px}
  .contact__lines svg{width:23px;height:23px;margin-right:16px;flex:none}
  .contact__web{margin-top:14px;font-family:'Open Sans',sans-serif;color:var(--gold);font-size:19px;letter-spacing:1px}
</style>
</head>
<body>

<section class="card card--front" aria-label="Card front">
  <span class="brand-dot"></span>
  <svg class="brand" style="left:262px;top:180px" width="510" height="200" aria-label="Ironhaven Security Systems Inc.">
    <text x="0" y="70" font-size="86" fill="#ffffff" textLength="500" lengthAdjust="spacingAndGlyphs">IRONHAVEN</text>
    <text x="0" y="115" font-size="44" fill="#ffffff" textLength="500" lengthAdjust="spacingAndGlyphs">SECURITY SYSTEMS INC.</text>
  </svg>
</section>

<section class="card card--back" aria-label="Card back">
  <span class="brand-dot"></span>
  <svg class="brand" style="left:89px;top:300px" width="290" height="90" aria-label="Ironhaven Security Systems Inc.">
    <text x="0" y="50" font-size="54" fill="#7b1416" textLength="283" lengthAdjust="spacingAndGlyphs">IRONHAVEN</text>
    <text x="0" y="74" font-size="28" fill="#7b1416" textLength="283" lengthAdjust="spacingAndGlyphs">SECURITY SYSTEMS INC.</text>
  </svg>

  <span class="divider"></span>

  <div class="contact">
    <p class="contact__name">Marcus Hale</p>
    <p class="contact__title">Owner</p>
    <p class="contact__address">PO Box your address<br>2nd Lane, WA 0000 USA</p>
    <ul class="contact__lines">
      <li>
        <svg viewBox="0 0 24 24" aria-hidden="true"><rect width="24" height="24" rx="4" fill="#e2b53e"/><path d="M5 9c0-2 3-3 7-3s7 1 7 3v1h-3V8.5h-8V10H5z M7 11h10l1 6H6z" fill="#fff"/><circle cx="12" cy="14" r="1.6" fill="#e2b53e"/></svg>
        555-014-2290
      </li>
      <li>
        <svg viewBox="0 0 24 24" aria-hidden="true"><rect width="24" height="24" rx="4" fill="#e2b53e"/><rect x="8" y="4" width="8" height="16" rx="1.5" fill="#fff"/><rect x="9.5" y="6" width="5" height="5" fill="#e2b53e"/></svg>
        +1 555-014-2291
      </li>
      <li>
        <svg viewBox="0 0 24 24" aria-hidden="true"><rect width="24" height="24" rx="4" fill="#e2b53e"/><rect x="4.5" y="7" width="15" height="10" fill="none" stroke="#fff" stroke-width="1.5"/><path d="M4.5 7l7.5 6 7.5-6" fill="none" stroke="#fff" stroke-width="1.5"/></svg>
        info@ironhavenus.com
      </li>
    </ul>
    <p class="contact__web">www.ironhavenus.com</p>
  </div>
</section>

</body>
</html>
```